Heron Haulage needs Bussiness cards!

Our new trucking company needs business cards!
We need the same design with two different names and emails, everything else it's the same.
I have included our original logo so we can use it for the design.
Note: the logo to be used is the o e with the buffalo on the right side, next to the letters H and H.

Target Market(s)

Trucking, refrigerated transportation, freight

Industry/Entity Type

Business

Contact Information for Business Card

Card #1:
Marcus Whitfield
marcuswhitfield@heronhaulage.example
1-855-317-6094
(956)238-7160
4117 W. Larkin Ave.
Pharr, TX 78590
www.heronhaulage.example

Card#2:
Rosalba Quintero
rosalba@heronhaulage.example
1-855-317-6094
(956)238-7160
4117 W. Larkin Ave.
Pharr, TX 78590
www.heronhaulage.example

Font styles to use
Sans Serif

Colors
0655a3
ec1f27
ffffff

Requirements
Must have
• our logo
Nice to have
• roads on background,

```html
<!DOCTYPE html>
<html lang="en">
<head>
<meta charset="utf-8">
<title>Heron Haulage — Business Card</title>
<link rel="stylesheet" href="https://fonts.googleapis.com/css2?family=Exo+2:wght@300;400&family=Lato:wght@300;400;700;900&display=swap">
<style>
  :root {
    --brand-blue: #0655a3;
    --brand-red: #ec1f27;
    --brand-navy: #10315f;
    --paper: #ffffff;
    --ink-grey: #8a8d92;
    --stage: #e9eaec;
  }
  * { box-sizing: border-box; margin: 0; padding: 0; }
  html, body { width: 1200px; height: 810px; overflow: hidden; }
  body {
    background: var(--stage);
    font-family: "Lato", sans-serif;
    position: relative;
  }
  .card {
    position: absolute;
    width: 540px;
    height: 310px;
    top: 250px;
    box-shadow: 0 10px 24px rgba(0,0,0,.18);
    overflow: hidden;
  }
  /* Front */
  .card--front { left: 40px; background: var(--brand-blue); color: var(--paper); }
  .card--front .wordmark {
    position: absolute; left: 0; right: 0; top: 108px;
    display: flex; align-items: center; justify-content: center; gap: 14px;
  }
  .wordmark__dot {
    width: 34px; height: 34px; border-radius: 50%;
    background: var(--paper);
  }
  .wordmark__name {
    font-family: "Lato", sans-serif; font-weight: 900;
    font-size: 44px; letter-spacing: .5px; line-height: 1;
  }
  .card--front .website {
    position: absolute; left: 0; right: 0; bottom: 44px;
    text-align: center; font-size: 13px; font-weight: 700; letter-spacing: .3px;
  }
  /* Back */
  .card--back { left: 620px; background: var(--paper); }
  .card--back .wordmark {
    position: absolute; right: 26px; top: 36px;
    display: flex; align-items: center; gap: 10px; color: var(--brand-navy);
  }
  .card--back .wordmark__dot { width: 24px; height: 24px; background: var(--brand-blue); }
  .card--back .wordmark__name { font-size: 30px; }
  .address {
    position: absolute; right: 22px; top: 150px;
    text-align: right; font-size: 12px; font-weight: 300; line-height: 1.5;
    color: var(--ink-grey);
  }
  .holder {
    position: absolute; left: 30px; top: 162px;
    font-family: "Exo 2", sans-serif; font-weight: 400;
    font-size: 23px; color: var(--brand-blue);
  }
  .contacts {
    position: absolute; left: 32px; top: 198px; list-style: none;
    font-size: 12.5px; font-weight: 300; color: var(--ink-grey); line-height: 1.45;
  }
  .contacts li { display: flex; align-items: center; gap: 8px; }
  .contacts svg { width: 11px; height: 11px; fill: var(--brand-navy); flex: none; }
  .edge-band { position: absolute; left: 0; bottom: 0; width: 540px; height: 24px; }
</style>
</head>
<body>
  <section class="card card--front" aria-label="Card front">
    <div class="wordmark">
      <span class="wordmark__dot"></span>
      <span class="wordmark__name">Heron Haulage</span>
    </div>
    <p class="website">www.heronhaulage.example</p>
  </section>

  <section class="card card--back" aria-label="Card back">
    <div class="wordmark">
      <span class="wordmark__dot"></span>
      <span class="wordmark__name">Heron Haulage</span>
    </div>

    <address class="address" style="font-style:normal">
      4117 W. Larkin Ave.<br>Pharr, TX 78590
    </address>

    <h1 class="holder">Marcus Whitfield</h1>

    <ul class="contacts">
      <li>
        <svg viewBox="0 0 24 24" aria-hidden="true"><path d="M6.6 10.8a15.1 15.1 0 0 0 6.6 6.6l2.2-2.2c.3-.3.7-.4 1-.2 1.1.4 2.3.6 3.6.6.6 0 1 .4 1 1V20c0 .6-.4 1-1 1A17 17 0 0 1 3 4c0-.6.4-1 1-1h3.5c.6 0 1 .4 1 1 0 1.3.2 2.5.6 3.6.1.3 0 .7-.2 1z"/></svg>
        1-855-317-6094
      </li>
      <li>
        <svg viewBox="0 0 24 24" aria-hidden="true"><path d="M7 1h10a2 2 0 0 1 2 2v18a2 2 0 0 1-2 2H7a2 2 0 0 1-2-2V3a2 2 0 0 1 2-2zm0 3v14h10V4zm5 15.5a1.2 1.2 0 1 0 0 2.4 1.2 1.2 0 0 0 0-2.4z"/></svg>
        (956)238-7160
      </li>
      <li>
        <svg viewBox="0 0 24 24" aria-hidden="true"><path d="M2 5h20v14H2zm2 2v.5l8 5 8-5V7zm0 2.8V17h16V9.8l-8 5z"/></svg>
        marcuswhitfield@heronhaulage.example
      </li>
      <li>
        <svg viewBox="0 0 24 24" aria-hidden="true"><path d="M12 2a10 10 0 1 0 0 20 10 10 0 0 0 0-20zm6.9 9h-3a15 15 0 0 0-1.3-5.6A8 8 0 0 1 18.9 11zM12 4.1c.9 1.2 1.8 3.6 1.9 6.9h-3.8c.1-3.3 1-5.7 1.9-6.9zM9.4 5.4A15 15 0 0 0 8.1 11h-3a8 8 0 0 1 4.3-5.6zM5.1 13h3a15 15 0 0 0 1.3 5.6A8 8 0 0 1 5.1 13zm6.9 6.9c-.9-1.2-1.8-3.6-1.9-6.9h3.8c-.1 3.3-1 5.7-1.9 6.9zm2.6-1.3a15 15 0 0 0 1.3-5.6h3a8 8 0 0 1-4.3 5.6z"/></svg>
        www.heronhaulage.example
      </li>
    </ul>

    <svg class="edge-band" viewBox="0 0 540 24" aria-hidden="true">
      <polygon points="0,10 338,10 332,24 0,24" fill="var(--brand-blue)"/>
      <polygon points="344,10 540,10 540,0 350,0" fill="var(--brand-red)" transform="translate(0,0)"/>
    </svg>
  </section>
</body>
</html>
```